Upmarket Dessert Lounge needs a Business Card Design

We are an upmarket dessert lounge needing a business card to match our image.

We want something that is simple yet beautiful, feminine, classy, sophisticated and elegant. We want it to stand out and don't mind if it is bold.

The design should include our logo and colours of red or maroon with gold highlights. We don't mind if black is used.

Marlow & Quince

Target Market(s)

For those who like to indulge or treat themselves and give in to their temptations on good quality desserts.

Industry/Entity Type

Business

Requirements
Must have
• Must include our logo and our name

Marlow & Quince

M & Q

```html
<!DOCTYPE html>
<html lang="en">
<head>
<meta charset="utf-8">
<title>Marlow &amp; Quince – Business Card</title>
<link href="https://fonts.googleapis.com/css2?family=Open+Sans:wght@400;600;700&display=swap" rel="stylesheet">
<style>
  :root {
    --maroon: #7b1416;
    --gold: #f6d9a4;
    --paper: #ffffff;
    --ink: #3a3a3a;
    --rule: #555555;
    --backdrop: #ece7e2;
  }
  * { box-sizing: border-box; margin: 0; padding: 0; }
  html, body {
    width: 1200px; height: 402px; overflow: hidden;
    background: var(--backdrop);
    font-family: "Open Sans", Arial, sans-serif;
  }
  .stage { position: relative; width: 1200px; height: 402px; }
  .card {
    position: absolute; top: 46px;
    width: 512px; height: 290px;
    border-radius: 22px; overflow: hidden;
    box-shadow: 0 4px 14px rgba(0,0,0,.18);
  }
  .card--front { left: 64px; background: var(--paper); }
  .card--back { left: 628px; background: var(--maroon); }

  .brand-name {
    position: absolute; top: 52px; left: 0; width: 100%;
    text-align: center; color: var(--maroon);
    font-size: 22px; font-weight: 600; letter-spacing: 1px;
    text-transform: uppercase;
  }
  .address {
    position: absolute; top: 158px; right: 272px;
    text-align: right; color: var(--ink);
    font-size: 12.5px; line-height: 17px;
  }
  .divider {
    position: absolute; left: 262px; top: 144px;
    width: 1px; height: 76px; background: var(--rule);
  }
  .contacts {
    position: absolute; left: 280px; top: 146px;
    list-style: none; color: var(--ink); font-size: 12.5px;
  }
  .contacts li { display: flex; align-items: center; height: 18.5px; }
  .contacts svg { width: 10px; height: 10px; margin-right: 6px; fill: var(--maroon); }
  .swoosh { position: absolute; left: 0; bottom: 0; width: 512px; height: 64px; }
  .person {
    position: absolute; left: 72px; bottom: 14px;
    color: #fff; font-size: 15px; font-weight: 700;
  }
  .person .title { font-weight: 400; font-size: 13px; }

  .monogram {
    position: absolute; inset: 0;
    display: flex; align-items: center; justify-content: center;
    color: var(--gold); font-size: 84px; font-weight: 400; letter-spacing: 2px;
  }
</style>
</head>
<body>
<main class="stage">
  <section class="card card--front" aria-label="Business card front">
    <div class="brand-name">Marlow &amp; Quince</div>

    <p class="address">Street Name, City Name<br>State Zip Code</p>
    <div class="divider"></div>
    <ul class="contacts">
      <li><svg viewBox="0 0 10 10"><path d="M2 0.5 L4 2.5 L3 3.8 Q4 6 6.2 7 L7.5 6 L9.5 8 L8 9.6 Q3 9 0.4 2 Z"/></svg>555-014-2368</li>
      <li><svg viewBox="0 0 10 10"><path d="M2.5 0 H7.5 V10 H2.5 Z M3.5 1.2 V6.5 H6.5 V1.2 Z"/></svg>555-014-2369</li>
      <li><svg viewBox="0 0 10 10"><path d="M0 2 H10 V8.5 H0 Z M0.8 2.6 L5 5.8 L9.2 2.6 Z" fill-rule="evenodd"/></svg>info@marlow&amp;quince.com</li>
      <li><svg viewBox="0 0 10 10"><circle cx="5" cy="5" r="4.4" fill="none" stroke="#7b1416" stroke-width="1"/><ellipse cx="5" cy="5" rx="1.9" ry="4.4" fill="none" stroke="#7b1416" stroke-width="0.9"/><path d="M0.6 5 H9.4" stroke="#7b1416" stroke-width="0.9"/></svg>www.marlow&amp;quince.com</li>
    </ul>

    <svg class="swoosh" viewBox="0 0 512 64" preserveAspectRatio="none" aria-hidden="true">
      <path d="M0 28 Q 200 8 512 40 L512 64 L0 64 Z" fill="var(--maroon)"/>
      <path d="M32 8 Q 200 -4 490 30" fill="none" stroke="var(--maroon)" stroke-width="2.2"/>
      <path d="M0 25 Q 210 4 512 36" fill="none" stroke="#fff" stroke-width="2.5"/>
    </svg>
    <p class="person">Your name, <span class="title">Title</span></p>
  </section>

  <section class="card card--back" aria-label="Business card back">
    <div class="monogram">M&amp;Q</div>
  </section>
</main>
</body>
</html>
```